Brightfen Business Card Redesign & Logo Update

We need to update our business cards to something more modern and fresh. Brightfen can provide the current color schemes and old design examples, but welcome creativity in helping us with this redesign. PLEASE NOTE that we no longer utilize the "tree" and/or "leaf" imagery in our branding. If able would apprecaite an update on the quality of our "words only" logo in Ai. / PNG formats too.

Target Market(s)

Investors, landowners, corporate partners, contractors

Industry/Entity Type

Environmental Restoration & Conservation

Contact Information for Business Card

Logo, persons name, title, mailing address, phone and email, website url

Font styles to use
Other font styles liked:
• Merriweather

Requirements
Nice to have
• Logo, persons name, title, mailing address, phone and email, website url, but open to ideams
Should not have
• No all back backgrounds

```html
<!DOCTYPE html>
<html lang="en">
<head>
<meta charset="utf-8">
<title>Brightfen Business Card</title>
<link href="https://fonts.googleapis.com/css2?family=Oswald:wght@500&family=Arimo:wght@400;700&display=swap" rel="stylesheet">
<style>
  :root {
    --page-bg: #e4e4e4;
    --card-white: #f8f8f8;
    --brand-orange: #e07b0a;
    --brand-green: #1a6b35;
    --logo-green: #2e9a5e;
    --back-green-top: #1b8244;
    --back-green-bottom: #0f6c31;
    --text-grey: #555555;
    --white: #ffffff;
  }
  * { margin: 0; padding: 0; box-sizing: border-box; }
  html, body {
    width: 1200px; height: 1200px; overflow: hidden;
    background: var(--page-bg);
  }
  .canvas { position: relative; width: 1200px; height: 1200px; }

  .card {
    position: absolute;
    left: 262px;
    width: 686px;
    height: 392px;
    border-radius: 21px;
    overflow: hidden;
    box-shadow: 0 10px 22px rgba(0,0,0,0.18);
  }
  .card--front { top: 165px; background: var(--card-white); }
  .card--back {
    top: 653px;
    background: linear-gradient(180deg, var(--back-green-top), var(--back-green-bottom));
  }

  /* Wordmark: name in the body text face with one plain square */
  .wordmark {
    display: flex;
    align-items: center;
    font-family: "Arimo", sans-serif;
    font-weight: 700;
    line-height: 1;
  }
  .wordmark__square { flex: none; }

  .front-logo {
    position: absolute;
    right: 41px;
    top: 68px;
    gap: 12px;
    font-size: 54px;
    color: var(--logo-green);
  }
  .front-logo .wordmark__square {
    width: 26px; height: 26px;
    background: var(--brand-orange);
  }

  /* Front: person */
  .person {
    position: absolute;
    left: 45px;
    top: 222px;
  }
  .person__name {
    font-family: "Oswald", sans-serif;
    font-weight: 500;
    font-size: 31px;
    line-height: 1.1;
    letter-spacing: -0.3px;
  }
  .person__first { color: var(--brand-orange); }
  .person__last { color: var(--brand-green); }
  .person__title {
    font-family: "Arimo", sans-serif;
    font-size: 15px;
    color: var(--text-grey);
    margin-top: 1px;
  }

  .divider {
    position: absolute;
    left: 45px;
    right: 41px;
    top: 285px;
    height: 1px;
    background: var(--brand-orange);
  }

  .contact {
    position: absolute;
    top: 294px;
    font-family: "Arimo", sans-serif;
    font-size: 16px;
    line-height: 20.5px;
    color: #3a3a3a;
    list-style: none;
  }
  .contact--left { left: 46px; }
  .contact--right { right: 41px; text-align: right; }
  .contact__item { display: flex; align-items: center; gap: 10px; }
  .contact__icon { width: 15px; height: 15px; flex: none; fill: var(--brand-orange); }

  /* Back */
  .back-logo {
    position: absolute;
    left: 0; right: 0;
    top: 150px;
    justify-content: center;
    gap: 18px;
    font-size: 84px;
    color: var(--white);
  }
  .back-logo .wordmark__square {
    width: 38px; height: 38px;
    background: var(--white);
  }
</style>
</head>
<body>
<main class="canvas">

  <section class="card card--front">
    <div class="wordmark front-logo">
      <span class="wordmark__square" aria-hidden="true"></span>
      <span class="wordmark__name">Brightfen</span>
    </div>

    <div class="person">
      <h1 class="person__name"><span class="person__first">DANIEL</span> <span class="person__last">MORROW</span></h1>
      <p class="person__title">Managing Director</p>
    </div>

    <div class="divider"></div>

    <ul class="contact contact--left">
      <li class="contact__item">
        <svg class="contact__icon" viewBox="0 0 24 24" aria-hidden="true"><path d="M6.6 10.8c1.4 2.8 3.8 5.1 6.6 6.6l2.2-2.2c.3-.3.7-.4 1-.2 1.1.4 2.3.6 3.6.6.6 0 1 .4 1 1V20c0 .6-.4 1-1 1C10.6 21 3 13.4 3 4c0-.6.4-1 1-1h3.5c.6 0 1 .4 1 1 0 1.3.2 2.5.6 3.6.1.3 0 .7-.2 1l-2.3 2.2z"/></svg>
        555-210-4832
      </li>
      <li class="contact__item">
        <svg class="contact__icon" viewBox="0 0 24 24" aria-hidden="true"><path d="M7 1h10a2 2 0 0 1 2 2v18a2 2 0 0 1-2 2H7a2 2 0 0 1-2-2V3a2 2 0 0 1 2-2zm0 3v14h10V4H7zm5 15.2a1.2 1.2 0 1 0 0 2.4 1.2 1.2 0 0 0 0-2.4z"/></svg>
        555-731-2096
      </li>
      <li class="contact__item">
        <svg class="contact__icon" viewBox="0 0 24 24" aria-hidden="true"><path d="M2 5h20v14H2V5zm2 2v.5l8 5 8-5V7H4zm0 2.9V17h16V9.9l-8 5-8-5z"/></svg>
        info@brightfen.com
      </li>
    </ul>

    <ul class="contact contact--right">
      <li>4120 Alderbrook Road</li>
      <li>Fairview, Oregon 97024</li>
      <li>www.brightfen.com</li>
    </ul>
  </section>

  <section class="card card--back">
    <div class="wordmark back-logo">
      <span class="wordmark__square" aria-hidden="true"></span>
      <span class="wordmark__name">Brightfen</span>
    </div>
  </section>

</main>
</body>
</html>
```